Dental Practice Billboard Design

We are a newer dental practice in need of a simple but appealing billboard for our growing dental practice to attract new patients. The practice is owned by husband and wife dentists and is family friendly in a small town in Kentucky. We try to be very friendly and caring to our patients. Would prefer a blue background for the billboard and our tooth logo to be prominent. We are partial to the Patua One font used in the image below but please feel free to tweak it as you deem necessary. The shape of the uppercase D and lowercase g are why we like that font, so fonts with a similarly shaped “D” and “g” would work as well. Please include our phone number (555) 847-1390. Please see our website Harlowbrookdentistry.example for more info on the practice if needed. Thank you! Looking forward to seeing your creation.
Updates

The dimensions will be 12ft x 24ft (3.6576m x 7.3152m). Apologies for not including this in the original prompt. Thank you all for your submissions.

Industry/Entity Type

Dental

Font styles to use
Other font styles liked:
• Patua One

Colors
0054AA
0677BA
7BADD7
CADEEF
E8F1F8
0094D4
00A9DD
6FCCEA
C7EBF8
E9F6FB
00AB8E
00BBA5
67D7C9
C6EFE9
E9F9F6
59FF00
82FF00
B8FF75
E3FFCB
F4FFEA

Requirements
Must have
• Phone number, website, Logo, Practice name “Harlow Brook Dentistry”
Should not have
• A tagline or slogan

```html
<!DOCTYPE html>
<html lang="en">
<head>
<meta charset="utf-8">
<title>Harlow Brook Dentistry Billboard</title>
<link rel="stylesheet" href="https://fonts.googleapis.com/css2?family=Patua+One&family=Montserrat:wght@800&family=Oswald:wght@600&display=swap">
<style>
  :root {
    --navy: #1e1f6e;
    --green: #16b418;
    --white: #ffffff;
    --page: #eef1f5;
    --photo-light: #e9ecf2;
    --photo-mid: #c9ced9;
  }
  * { margin: 0; padding: 0; box-sizing: border-box; }
  html, body { width: 1200px; height: 857px; overflow: hidden; background: var(--page); }
  .billboard {
    position: absolute; left: 40px; top: 148px;
    width: 1120px; height: 560px;
    background: var(--navy); overflow: hidden;
  }
  .team-photo {
    position: absolute; left: 0; top: 48px;
    width: 390px; height: 380px;
    background: linear-gradient(160deg, var(--photo-light) 0%, var(--photo-mid) 100%);
  }
  .bands { position: absolute; left: 0; top: 0; width: 1120px; height: 560px; }
  .brand {
    position: absolute; left: 440px; top: 110px;
    width: 660px; height: 280px;
    display: flex; align-items: center; justify-content: center; gap: 28px;
  }
  .brand-dot {
    flex: none; width: 70px; height: 70px; border-radius: 50%; background: var(--green);
  }
  .brand-name {
    font-family: "Patua One", serif; font-size: 84px; line-height: 1.05;
    color: var(--white);
  }
  .phone {
    position: absolute; left: 40px; top: 455px;
    display: flex; align-items: center; gap: 16px;
    font-family: "Montserrat", sans-serif; font-weight: 800; font-size: 50px; color: var(--white);
  }
  .phone-icon { width: 56px; height: 56px; }
  .website {
    position: absolute; right: 30px; top: 504px;
    font-family: "Oswald", sans-serif; font-weight: 600; font-size: 32px; line-height: 48px;
    color: var(--navy); letter-spacing: 0.5px; white-space: nowrap;
  }
</style>
</head>
<body>
  <div class="billboard">
    <div class="team-photo" role="img" aria-label="Photo of the two dentists in white coats, smiling"></div>

    <svg class="bands" viewBox="0 0 1120 560" aria-hidden="true">
      <path d="M0 424 L520 424 Q560 424 582 460 L640 560 L0 560 Z" fill="var(--green)"/>
      <path d="M575 496 L1120 496 L1120 560 L620 560 Z" fill="var(--white)"/>
    </svg>

    <div class="brand">
      <span class="brand-dot"></span>
      <span class="brand-name">Harlow Brook<br>Dentistry</span>
    </div>

    <div class="phone">
      <svg class="phone-icon" viewBox="0 0 56 56" aria-hidden="true">
        <circle cx="28" cy="28" r="27" fill="var(--white)"/>
        <path d="M19 14c2 0 3 1 4 3l2 5c.5 1.5 0 2.5-1 3.5l-2 2c1.5 3.5 4 6 7.5 7.5l2-2c1-1 2-1.5 3.5-1l5 2c2 1 3 2 3 4v3c0 2-2 4-4 4C25 45 11 31 11 18c0-2 2-4 4-4z" fill="var(--green)"/>
      </svg>
      <span>(555) 847-1390</span>
    </div>

    <div class="website">HARLOWBROOKDENTISTRY.EXAMPLE</div>
  </div>
</body>
</html>
```